Corporate Values project needs own identity (logo, illustrations, font)

For a project to liven up corporate values we have designed 10 questions our employees should ask themselves at any time. To start marketing these, we want to have various outings (posters, cards, leaflets, etc) that illustrate these questions. preferably with a logo / font of its own. Look and feel / moodwords: insurance, blue, values, non negociable, fun, vintage, together. The 10 questions are:
1. What would the customer say?
2. How will this help those of us in front of the customer?
3. Have I expressed my views clearly and openly?
4. How can we do this differently and to higher standards? Better, faster, simpler?
5. How can I help, beyond my specific role description?
6. Have I recognised other people’s contributions and ideas?
7. Am I keeping my commitments to others, internal or externally?
8. How can I learn more? And how can I share more so others can learn form this?
9. Who needs, and who does not need to be involved?
10. Is there a different or alternative view, opinion or option?

Preferably, each question gets its own little ilustration.

If things are not clear, or more information needed, please let me know.

Reason: Since part of the project has been postponed, we can take more time for the design.

```html
<!DOCTYPE html>
<html lang="en">
<head>
<meta charset="utf-8">
<title>Question 1 of 10 – What would the customer say?</title>
<link rel="stylesheet" href="https://fonts.googleapis.com/css2?family=Antonio:wght@100;200&family=Bebas+Neue&display=swap">
<style>
  :root {
    --teal: #00b2b4;
    --cyan: #00ffff;
    --track: #19d3d6;
    --white: #ffffff;
    --illustration-fill: #14c3c6;
  }
  * { margin: 0; padding: 0; box-sizing: border-box; }
  html, body {
    width: 1200px;
    height: 1000px;
    overflow: hidden;
    background: var(--teal);
  }
  .question-card {
    position: relative;
    width: 1200px;
    height: 1000px;
    background: var(--teal);
    color: var(--white);
  }
  .progress {
    position: absolute;
    left: 37px;
    top: 37px;
    width: 808px;
    height: 7px;
    background: var(--track);
  }
  .progress__done {
    display: block;
    width: 81px;
    height: 100%;
    background: var(--cyan);
  }
  .counter {
    position: absolute;
    left: 41px;
    top: 72px;
    font-family: "Antonio", "Arial Narrow", sans-serif;
    font-weight: 200;
    font-size: 55px;
    line-height: 1;
    color: var(--cyan);
  }
  .question {
    position: absolute;
    left: 36px;
    top: 180px;
    line-height: 1;
    text-transform: uppercase;
  }
  .question__lead {
    display: block;
    font-family: "Antonio", "Arial Narrow", sans-serif;
    font-weight: 100;
    font-size: 147px;
    line-height: 1;
    letter-spacing: -1px;
  }
  .question__main {
    display: block;
    margin-top: 0;
    font-family: "Bebas Neue", "Arial Narrow", sans-serif;
    font-weight: 400;
    font-size: 152px;
    line-height: 1;
    letter-spacing: 1px;
  }
  .illustration {
    position: absolute;
    left: 36px;
    top: 548px;
    width: 250px;
    height: 350px;
    background: var(--illustration-fill);
    border-radius: 12px;
  }
</style>
</head>
<body>
  <main class="question-card">
    <div class="progress" aria-label="Question 1 of 10">
      <span class="progress__done"></span>
    </div>
    <p class="counter">1/10</p>
    <h1 class="question">
      <span class="question__lead">What would</span>
      <span class="question__main">The customer say?</span>
    </h1>
    <div class="illustration" role="img" aria-label="Line illustration of a customer in a shirt and tie with a speech bubble containing three dots"></div>
  </main>
</body>
</html>
```